RW Framewell Inc Business cards

We need business cards using our existing logo but slightly modified. Right now the logo says RW Loadbearing Masonry. We want to keep the RW part of the design, but replace the Structural Concrete portion with "FRAMEWELL". Please see the attached file.
Ideally this would be a blank template so we can add Different Names, titles, and phone numbers later.
On the one side we want only the logo and on the other side the detail. I'm attaching an example for you to see.
Please reach out with any other questions. Our address and other details will be given out once we find a design we like.

Target Market(s)

Construction Industry

```html
<!DOCTYPE html>
<html lang="en">
<head>
<meta charset="UTF-8">
<title>RW Framewell Inc — Business Cards</title>
<link rel="stylesheet" href="https://fonts.googleapis.com/css2?family=Exo+2:wght@400;600&family=Open+Sans:wght@400&display=swap">
<style>
  :root {
    --stage: #1e1e1e;
    --brand-blue: #1474c4;
    --brand-blue-soft: #2a84cf;
    --brand-grey: #7b7d80;
    --text-grey: #6d6f72;
    --card-white: #ffffff;
  }
  * { margin: 0; padding: 0; box-sizing: border-box; }
  html, body { width: 1200px; height: 900px; overflow: hidden; }
  body {
    background: var(--stage);
    position: relative;
    font-family: "Open Sans", sans-serif;
  }
  .card {
    position: absolute;
    left: 290px;
    width: 620px;
    height: 354px;
    overflow: hidden;
  }
  .card--front {
    top: 60px;
    background: linear-gradient(135deg, var(--brand-blue-soft), var(--brand-blue));
    display: flex;
    align-items: center;
    justify-content: center;
  }
  .front-pattern {
    position: absolute;
    inset: 0;
    background: linear-gradient(135deg, #2a86d2, #1872c0);
  }
  .front-wordmark {
    position: relative;
    font-family: "Exo 2", sans-serif;
    font-weight: 600;
    font-size: 44px;
    letter-spacing: 3px;
    color: var(--card-white);
  }
  .card--back {
    top: 470px;
    background: var(--card-white);
  }
  .back-wordmark {
    position: absolute;
    left: 38px;
    top: 126px;
    width: 230px;
    font-family: "Exo 2", sans-serif;
    font-weight: 600;
    font-size: 38px;
    line-height: 1.05;
    letter-spacing: 2px;
    color: var(--brand-blue);
  }
  .divider {
    position: absolute;
    left: 300px;
    top: 80px;
    width: 2px;
    height: 150px;
    background: var(--brand-blue);
  }
  .person {
    position: absolute;
    left: 330px;
    top: 76px;
  }
  .person-name {
    font-family: "Exo 2", sans-serif;
    font-weight: 400;
    font-size: 28px;
    letter-spacing: 2px;
    color: var(--brand-blue);
    line-height: 1;
  }
  .person-title {
    font-size: 17px;
    color: var(--text-grey);
    margin-top: 2px;
  }
  .contacts {
    position: absolute;
    left: 330px;
    top: 150px;
    list-style: none;
  }
  .contacts li {
    display: flex;
    align-items: center;
    gap: 10px;
    font-size: 17px;
    line-height: 26px;
    color: var(--text-grey);
  }
  .contacts svg { width: 16px; height: 16px; fill: var(--brand-blue); flex: none; }
  .band-blue {
    position: absolute;
    left: 0;
    bottom: 0;
    width: 340px;
    height: 18px;
    background: var(--brand-blue);
  }
  .band-address {
    position: absolute;
    right: 0;
    bottom: 0;
    width: 310px;
    height: 50px;
    background: var(--brand-grey);
    border-top-left-radius: 18px;
    color: var(--card-white);
    font-size: 18px;
    line-height: 50px;
    padding-left: 26px;
  }
</style>
</head>
<body>
  <section class="card card--front">
    <div class="front-pattern" role="img" aria-label="Faint repeating brand pattern in tones of blue"></div>
    <div class="front-wordmark">RW FRAMEWELL</div>
  </section>

  <section class="card card--back">
    <div class="back-wordmark">RW<br>FRAMEWELL</div>
    <div class="divider"></div>
    <div class="person">
      <p class="person-name">DANA HOLLIS</p>
      <p class="person-title">Chief Officer</p>
    </div>
    <ul class="contacts">
      <li><svg viewBox="0 0 16 16"><path d="M3.5 1l2.5 3-1.5 1.5a9 9 0 0 0 6 6L12 10l3 2.5-1.5 2.5C7 15 1 9 1 2.5z"/></svg>+00 8 38 00 00</li>
      <li><svg viewBox="0 0 16 16"><path d="M4 0h8v16H4zM5.5 1.5v11h5v-11zM7 13.5h2v1H7z" fill-rule="evenodd"/></svg>+00 0 90 00 00</li>
      <li><svg viewBox="0 0 16 16"><path d="M0 3h16v10H0zM1.5 4.5L8 9l6.5-4.5v-.2h-13z"/></svg>info@rwframewell.com</li>
      <li><svg viewBox="0 0 16 16"><path d="M8 0a8 8 0 1 0 0 16A8 8 0 0 0 8 0zm0 1.5c1 1 1.8 3 2 5.5H6c.2-2.5 1-4.5 2-5.5zM1.6 7a6.5 6.5 0 0 1 3-4.8C4 3.7 4.6 5.3 4.5 7zm0 2h2.9c.1 1.7.5 3.3 1.1 4.8A6.5 6.5 0 0 1 1.6 9zM6 9h4c-.2 2.5-1 4.5-2 5.5-1-1-1.8-3-2-5.5zm5.5 0h2.9a6.5 6.5 0 0 1-4 4.8c.6-1.5 1-3.1 1.1-4.8zm0-2c-.1-1.7-.5-3.3-1.1-4.8A6.5 6.5 0 0 1 14.4 7z"/></svg>www.rwframewell.com</li>
    </ul>
    <div class="band-blue"></div>
    <div class="band-address">Your address line here. Country</div>
  </section>
</body>
</html>
```